Retail/Wholesale website graphic template

I need to design a new graphic template for a website for a client. The website will be a retail/wholesale company site with most pages dedicated to presentation. There will also be an online store and a blog. However, you don't need to worry about those. All I need from you is a graphic template for a generic site page.

It will need to include standard UI elements, in case I need those. I am attaching a more detailed assignment in .docx format.

The logo is also attached.

Target Market(s)

small business owners, (occasional) retail customers

Industry/Entity Type

Wholesale

Number of Pages Required

1 page

Font styles to use
Serif
Sans Serif

Colors
ec1f27
474747

Requirements
Must have
• must match logo, be clean, minimal and with slightly larger text size
Should not have
• must not be modern-looking where you have to scroll and scroll and scroll to get to the bottom of the homepage. most of my visitors are "old" people, they do not get this type of design.

```html
<!DOCTYPE html>
<html lang="en">
<head>
<meta charset="utf-8">
<title>Corval Imports</title>
<link rel="stylesheet" href="https://fonts.googleapis.com/css2?family=Open+Sans:wght@400;600;700;800&display=swap">
<style>
:root{
  --red:#ec1f27;
  --red-deep:#c9141b;
  --ink:#474747;
  --dark:#2b2b2b;
  --footer:#2e2e2e;
  --light:#f4f4f4;
  --muted:#8a8a8a;
  --white:#ffffff;
}
*{box-sizing:border-box;margin:0;padding:0}
html,body{width:1200px;height:3622px;overflow:hidden}
body{font-family:"Open Sans",Arial,sans-serif;color:var(--ink);background:var(--white);position:relative}
section,header,footer,.topbar{position:absolute;left:0;width:1200px}
.abs{position:absolute}

.topbar{top:0;height:46px;background:var(--dark);color:#ddd;font-size:12px}
.topbar .links{position:absolute;right:100px;top:14px;display:flex;gap:22px}

.site-header{top:46px;height:111px;background:var(--white)}
.brand{position:absolute;left:97px;top:26px;font-weight:800;font-size:30px;letter-spacing:3px;color:var(--ink);line-height:1}
.brand small{display:block;font-size:13px;letter-spacing:8px;margin-top:6px;font-weight:800}
.nav{position:absolute;right:98px;top:46px;display:flex;gap:43px;font-size:13px;font-weight:600;color:#333;text-transform:uppercase}
.nav .active{color:var(--red);border-bottom:2px solid var(--red);padding-bottom:6px}

.hero{top:157px;height:620px;background:linear-gradient(180deg,#6a6d70 0%,#8b8c86 40%,#5b5a55 100%)}
.hero h1{position:absolute;top:165px;width:100%;text-align:center;color:#fff;font-size:78px;font-weight:800;letter-spacing:6px}
.hero p{position:absolute;top:255px;width:100%;text-align:center;color:#fff;font-size:22px;letter-spacing:3px}
.hero .arrow{position:absolute;top:220px;width:40px;height:40px;border-radius:50%;background:rgba(255,255,255,.18)}

.welcome{top:720px;height:438px}
.welcome .frame{position:absolute;left:101px;top:48px;width:997px;height:318px;border:14px solid rgba(255,255,255,.08);background:rgba(0,0,0,.03)}
.welcome h2{position:absolute;top:66px;width:100%;text-align:center;color:#fff;font-size:36px;font-weight:700}
.welcome p{position:absolute;left:135px;width:930px;text-align:center;color:#fff;font-size:14px;line-height:24px}
.btn-line{position:absolute;left:519px;top:311px;width:162px;height:43px;border:2px solid #fff;color:#fff;font-size:14px;font-weight:600;text-align:center;line-height:39px}

.title{position:absolute;width:100%;text-align:center;font-size:36px;font-weight:700;color:var(--ink)}
.title::after{content:"";display:block;width:76px;height:3px;background:var(--red);margin:10px auto 0}
.title.on-red{color:#fff}
.title.on-red::after{background:#fff}

.services{top:1158px;height:628px;background:var(--light)}
.service{position:absolute;top:188px;width:240px;text-align:center}
.service .icon{width:116px;height:116px;border-radius:50%;background:#fff;border:1px solid #e6e6e6;margin:0 auto;display:flex;align-items:center;justify-content:center}
.service.active .icon{background:var(--red);border-color:var(--red)}
.service h3{font-size:19px;font-weight:600;color:#222;margin-top:20px}
.service.active h3{color:var(--red)}
.service p{font-size:13px;line-height:20px;color:var(--muted);margin-top:8px;padding:0 22px}
.btn-red{position:absolute;background:var(--red);color:#fff;font-size:14px;font-weight:600;text-align:center}

.support{top:1786px;height:452px;background:linear-gradient(90deg,rgba(200,20,27,.92),rgba(236,31,39,.88)),linear-gradient(180deg,#6b2a2a,#9a4040)}
.support ul{position:absolute;left:220px;top:150px;list-style:none}
.support li{color:#fff;font-size:24px;height:52px;display:flex;align-items:center;gap:14px}
.support li::before{content:"";width:26px;height:26px;border:3px solid #fff;border-radius:50%;flex:none}

.blog{top:2238px;height:606px;background:#f7f7f7}
.post{position:absolute;top:176px;width:302px;height:234px;border:6px solid #fff;box-shadow:0 0 0 1px #e4e4e4}
.post .pic{position:absolute;inset:0}
.post h4{position:absolute;left:12px;right:12px;color:#fff;font-size:18px;font-weight:800;line-height:22px;text-transform:uppercase}
.post time{position:absolute;left:12px;color:#eee;font-size:11px}
.post .more{position:absolute;left:12px;color:#fff;font-size:11px;font-weight:700}

.partners{top:2844px;height:398px;background:#fff}
.partner{position:absolute;top:186px;width:180px;height:120px;border:1px solid #d9d9d9;box-shadow:0 2px 4px rgba(0,0,0,.08);display:flex;align-items:center;justify-content:center;gap:8px;font-size:19px;font-weight:700;color:#3c3c3c}
.partner .sq{width:12px;height:12px;background:#3c3c3c}
.partners .chev{position:absolute;top:226px}

.site-footer{top:3242px;height:380px;background:var(--footer);color:#ddd}
.site-footer .brand{left:99px;top:124px;color:#fff}
.col{position:absolute;top:78px;font-size:13px;line-height:32px}
.col h5{font-size:17px;font-weight:600;color:#fff;margin-bottom:10px;line-height:24px}
.col.contact{line-height:26px}
.social{display:flex;gap:10px;margin-top:24px}
.social span{width:18px;height:18px;border-radius:50%;background:#e5e5e5}
.copy{position:absolute;left:97px;right:97px;top:307px;border-top:1px solid #444;padding-top:26px;text-align:center;font-size:12px;color:#bbb}
</style>
</head>
<body>

<div class="topbar">
  <div class="links"><span>☎ (001) 555-0142</span><span>✉ info@corvalmail.com</span><span>Login</span><span>SignUp</span></div>
</div>

<header class="site-header">
  <div class="brand">CORVAL<small>IMPORTS</small></div>
  <nav class="nav">
    <span class="active">Home</span><span>About Us</span><span>Our Services ▾</span><span>Support</span><span>Blog</span><span>Partners</span><span>Contact Us</span>
  </nav>
</header>

<section class="hero" role="img" aria-label="Warehouse aisle with workers in red overalls and a pallet truck among stacked boxes">
  <h1>CORVAL IMPORTS</h1>
  <p>We are a retail &amp; whole sale import company</p>
  <span class="arrow" style="left:20px"></span>
  <span class="arrow" style="right:20px"></span>
</section>

<section class="welcome">
  <svg class="abs" style="left:0;top:0" width="1200" height="438" viewBox="0 0 1200 438"><path d="M0 40 Q600 -20 1200 40 L1200 438 L0 438 Z" fill="#ec1f27"/></svg>
  <div class="frame"></div>
  <h2>WELCOME TO <span style="border-bottom:3px solid #fff">CORVAL</span> IMPORTS</h2>
  <p style="top:130px">Sed ut perspiciatis unde omnis iste natus error sit voluptatem accusantium doloremque laudantium, totam rem aperiam, eaque ipsa quae ab illo inventore veritatis et quasi architecto beatae vitae dicta sunt explicabo. Nemo enim ipsam voluptatem quia voluptas sit aspernatur aut odit aut fugit, sed quia consequuntur magni dolores eos qui ratione voluptatem sequi nesciunt.</p>
  <p style="top:220px">But I must explain to you how all this mistaken idea of denouncing pleasure and praising pain was born and I will give you a complete account of the system, and expound the actual teachings of the great explorer of the truth, the master-builder of human happiness.</p>
  <div class="btn-line">LEARN MORE</div>
</section>

<section class="services">
  <h2 class="title" style="top:70px">OUR SERVICES</h2>
  <div class="service" style="left:71px">
    <div class="icon"><svg width="56" height="56" viewBox="0 0 56 56" fill="none" stroke="#ec1f27" stroke-width="2.5"><path d="M8 22 L12 10 H44 L48 22 Z"/><path d="M8 22 Q14 28 20 22 Q28 28 36 22 Q42 28 48 22"/><path d="M12 26 V46 H44 V26"/><rect x="23" y="32" width="10" height="14"/></svg></div>
    <h3>Retail Store</h3>
    <p>Temporibus autem quibusdam et aut officiis debitis aut rerum necessitatibus saepe eveniet ut et voluptates repudiandae.</p>
  </div>
  <div class="service" style="left:343px">
    <div class="icon"><svg width="56" height="56" viewBox="0 0 56 56" fill="none" stroke="#ec1f27" stroke-width="2.5"><path d="M18 22 L26 8 M38 22 L30 8"/><rect x="6" y="22" width="44" height="6"/><path d="M10 28 L14 48 H42 L46 28"/><path d="M20 32 V44 M28 32 V44 M36 32 V44"/></svg></div>
    <h3>Whole Sale</h3>
    <p>Temporibus autem quibusdam et aut officiis debitis aut rerum necessitatibus saepe eveniet ut et voluptates repudiandae.</p>
  </div>
  <div class="service active" style="left:616px">
    <div class="icon"><svg width="56" height="56" viewBox="0 0 56 56" fill="none" stroke="#fff" stroke-width="2.5"><circle cx="28" cy="16" r="6"/><circle cx="14" cy="22" r="5"/><circle cx="42" cy="22" r="5"/><path d="M18 46 V32 Q28 24 38 32 V46"/><path d="M6 44 V34 Q10 29 16 31 M50 44 V34 Q46 29 40 31"/></svg></div>
    <h3>Distribution Services</h3>
    <p>Temporibus autem quibusdam et aut officiis debitis aut rerum necessitatibus saepe eveniet ut et voluptates repudiandae.</p>
  </div>
  <div class="service" style="left:889px">
    <div class="icon"><svg width="56" height="56" viewBox="0 0 56 56" fill="none" stroke="#ec1f27" stroke-width="2.5"><path d="M4 24 L14 14 L22 20 L30 16 L42 16 L52 26"/><path d="M14 30 L26 42 Q30 44 32 40 L38 36 L46 28"/><path d="M24 24 L30 20 L40 30"/></svg></div>
    <h3>Other Services</h3>
    <p>Temporibus autem quibusdam et aut officiis debitis aut rerum necessitatibus saepe eveniet ut et voluptates repudiandae.</p>
  </div>
  <div class="btn-red" style="left:521px;top:503px;width:157px;height:41px;line-height:41px">VIEW MORE</div>
</section>

<section class="support" role="img" aria-label="Red-tinted warehouse shelving in the background">
  <h2 class="title on-red" style="top:62px">OUR SUPPORT</h2>
  <ul>
    <li>Excepteur sint occaecat cupidatat non proident, sunt in culpa qui officia.</li>
    <li>But I must explain to you how all this mistaken idea of denouncing pleasure.</li>
    <li>At vero eos et accusamus et iusto odio dignissimos ducimus qui blanditiis.</li>
    <li>Temporibus autem quibusdam et aut officiis debitis aut rerum necessitatibus.</li>
  </ul>
</section>

<section class="blog">
  <h2 class="title" style="top:68px">OUR BLOG</h2>
  <article class="post" style="left:101px">
    <div class="pic" role="img" aria-label="Business people standing in a warehouse" style="background:linear-gradient(180deg,#9a9890,#5e5c58)"></div>
    <h4 style="top:126px">Nostrum exercitationem ullam corporis</h4>
    <time style="top:178px">APRIL 14, 2015</time>
  </article>
  <article class="post" style="left:449px">
    <div class="pic" role="img" aria-label="Stacked cardboard boxes in a dim storage room" style="background:linear-gradient(180deg,#3a3836,#6c645a)"></div>
    <h4 style="top:70px">Eiusmod tempor incididunt ut labore</h4>
    <time style="top:120px">JANUARY 20, 2015</time>
    <span class="more" style="top:160px">READ MORE ⊕</span>
  </article>
  <article class="post" style="left:794px">
    <div class="pic" role="img" aria-label="Shipping containers stacked at a cargo port" style="background:linear-gradient(180deg,#8a7f78,#6b4a3c)"></div>
    <h4 style="top:126px">Numquam eius modi tempora incidunt</h4>
    <time style="top:178px">APRIL 14, 2015</time>
  </article>
  <div class="btn-red" style="left:524px;top:485px;width:152px;height:41px;line-height:41px;font-size:13px">VIEW ALL BLOG</div>
</section>

<section class="partners">
  <h2 class="title" style="top:62px">CLIENT PARTNER</h2>
  <svg class="chev" style="left:78px" width="18" height="40" viewBox="0 0 18 40"><path d="M16 2 L2 20 L16 38" fill="none" stroke="#ccc" stroke-width="2"/></svg>
  <div class="partner" style="left:116px"><span class="sq"></span>Larkfield</div>
  <div class="partner" style="left:314px">Brightway</div>
  <div class="partner" style="left:509px">Orchardine</div>
  <div class="partner" style="left:705px">Novel Goods</div>
  <div class="partner" style="left:903px"><span class="sq"></span>Tessaro</div>
  <svg class="chev" style="left:1102px" width="18" height="40" viewBox="0 0 18 40"><path d="M2 2 L16 20 L2 38" fill="none" stroke="#ccc" stroke-width="2"/></svg>
</section>

<footer class="site-footer">
  <div class="brand">CORVAL<small>IMPORTS</small></div>
  <div class="col" style="left:365px"><h5>Product Gallery</h5>Deserunt Mollit<br>Occaecat Cupidatat<br>Accusantium<br>Doloremque<br>consequuntur Magni</div>
  <div class="col" style="left:596px"><h5>Our Process</h5>Inventore Veritatis<br>Quasi Architecto<br>Beatae Vitae<br>Dicta Sunt</div>
  <div class="col" style="left:794px"><h5>&nbsp;</h5>Site Map<br>Privacy Policy</div>
  <div class="col contact" style="left:934px"><h5>Contact Us</h5>⌖ Corval Imports, Street Name,<br>&nbsp;&nbsp;&nbsp;City Address, Country Code.<br>☎ (001) 555-0142<br>✉ info@corvalmail.com
    <div class="social"><span></span><span></span><span></span><span></span><span></span><span></span></div>
  </div>
  <div class="copy">© 2018 CORVAL IMPORTS. All right reserved . Term of Use</div>
</footer>

</body>
</html>
```